Graphic Design/Logo Needed for Ear Drops Bottle

We have an Ear Drop Medication that we need to create a new label for. We will use a retro picture of a Doctor (Dr. Bellamy) and the name of the product is Mighty Lobe. There is no official logo, so we will want to create a retro, basic logo for Mighty Lobe and use the retro picture. Front portion of the label is Size is 1.5" in height, and about 1.375" Width. this is a small tube similar in size to eye drops. We will be looking for just the logo portion and what you will see on the front of the bottle.

Target Market(s)

Medical Container

Industry/Entity Type

Medical

Font styles to use
Serif
Sans Serif

Colors
0054AA
0677BA
7BADD7
CADEEF
E8F1F8
FFF300
FFF600
FEFA6F
FFFEC7
FFFEE8

Requirements
Must have
• Picture of Dr. Bellamy, "Mighty Lobe", Dr. Bellamy's Ear Solution
Nice to have
• Retro Style or Modern with Retro Feel, Clean and engaging

```html
<!DOCTYPE html>
<html lang="en">
<head>
<meta charset="utf-8">
<title>Mighty Lobe – Ear Solution Label</title>
<link rel="stylesheet" href="https://fonts.googleapis.com/css2?family=Teko:wght@500&family=Montserrat:wght@600&display=swap">
<style>
  :root {
    --brand-blue: #0677BA;
    --deep-blue: #0054AA;
    --frame-blue: #7BADD7;
    --badge-yellow: #FFF300;
    --paper: #FFFFFF;
  }
  * { margin: 0; padding: 0; box-sizing: border-box; }
  html, body {
    width: 1200px;
    height: 773px;
    overflow: hidden;
    background: var(--paper);
  }
  .canvas {
    position: relative;
    width: 1200px;
    height: 773px;
    background: var(--paper);
  }
  .label {
    position: absolute;
    left: 287px;
    top: 46px;
    width: 625px;
    height: 680px;
    background: var(--paper);
    border: 1px solid var(--frame-blue);
    overflow: hidden;
  }
  .label-band {
    position: absolute;
    inset: 0;
    width: 100%;
    height: 100%;
  }
  .doctor-portrait {
    position: absolute;
    left: 164px;
    top: 64px;
    width: 296px;
    height: 233px;
    border-radius: 46% 46% 8px 8px / 60% 60% 8px 8px;
    background: linear-gradient(180deg, var(--deep-blue) 0%, #1a5f9e 60%, #3d7fb8 100%);
  }
  .product-name {
    position: absolute;
    left: 0;
    width: 100%;
    top: 282px;
    text-align: center;
    font-family: "Teko", "Arial Narrow", sans-serif;
    font-weight: 500;
    font-size: 112px;
    line-height: 1;
    color: var(--brand-blue);
    letter-spacing: 0.5px;
  }
  .product-subtitle {
    position: absolute;
    left: 0;
    width: 100%;
    top: 387px;
    text-align: center;
    font-family: "Montserrat", Arial, sans-serif;
    font-weight: 600;
    font-size: 26px;
    line-height: 33px;
    color: var(--brand-blue);
  }
  .net-weight {
    position: absolute;
    left: 0;
    width: 100%;
    top: 594px;
    display: flex;
    justify-content: center;
    align-items: center;
    gap: 8px;
    font-family: "Teko", "Arial Narrow", sans-serif;
    font-weight: 500;
    font-size: 30px;
    line-height: 1;
    color: var(--paper);
  }
  .net-weight-badge {
    width: 56px;
    height: 56px;
    border-radius: 50%;
    background: var(--badge-yellow);
    color: var(--deep-blue);
    display: flex;
    align-items: center;
    justify-content: center;
    font-size: 34px;
    padding-top: 5px;
  }
  .net-weight-text { padding-top: 5px; }
</style>
</head>
<body>
  <main class="canvas">
    <section class="label">
      <svg class="label-band" viewBox="0 0 625 680" preserveAspectRatio="none" aria-hidden="true">
        <path d="M0 436 Q 300 612 625 428 L625 680 L0 680 Z" fill="var(--brand-blue)"/>
      </svg>

      <div class="doctor-portrait" role="img" aria-label="Retro portrait illustration of Dr. Bellamy wearing a head mirror"></div>

      <h1 class="product-name">Mighty Lobe</h1>
      <p class="product-subtitle">DR BELLAMY’S<br>EAR SOLUTION</p>

      <div class="net-weight">
        <span class="net-weight-text">Nt. Wt.</span>
        <span class="net-weight-badge">2oz</span>
        <span class="net-weight-text">59 ml</span>
      </div>
    </section>
  </main>
</body>
</html>
```